Need logo and design for business card "FernGlen Plumbing Services".

Needing a design for plumbing company 'FernGlen Plumbing Services', a company based on the surfcoast.
Would like the colour black and blue incorporated. We offer free quotes and reliable friendly service, but don't want this writing on front of card.

I do not have a logo so wanting ideas. Any logo ideas on it would be great.

Target Market(s)

People wanting a Plumber

Industry/Entity Type

Business

Requirements
Must have
• Domestic Plumbing
• Commercial Plumbing
• Roofing
• Gasfitting
Nice to have
• Maybe some sort of plumbing picture on it, spanner, toilet, tap with water etc. Just relating to plumbing.
• FernGlen is on word also with the capital A in it.

```html
<!DOCTYPE html>
<html lang="en">
<head>
<meta charset="utf-8">
<title>FernGlen Plumbing Services – Business Card</title>
<link href="https://fonts.googleapis.com/css2?family=Montserrat:wght@500;600&display=swap" rel="stylesheet">
<style>
  :root {
    --backdrop: #e9e6e1;
    --card: #0b0b0c;
    --card-edge: #1c1c1f;
    --brand: #b9d2ea;
    --text: #f2f2f2;
    --muted: #bdbdbd;
    --rule: #d8d8d8;
  }
  * { margin: 0; padding: 0; box-sizing: border-box; }
  html, body { width: 1200px; height: 1000px; overflow: hidden; }
  body {
    background: var(--backdrop);
    font-family: "Montserrat", Arial, sans-serif;
    position: relative;
  }
  .card {
    position: absolute;
    width: 560px;
    height: 320px;
    background: linear-gradient(160deg, var(--card-edge) 0%, var(--card) 45%, var(--card) 100%);
    border-radius: 4px;
    box-shadow: 0 10px 28px rgba(0,0,0,0.28);
    overflow: hidden;
  }
  .card--front { left: 90px; top: 130px; }
  .card--back { left: 550px; top: 540px; }

  /* Company name: one colour, one weight, plain circle beside it */
  .company {
    display: flex;
    align-items: center;
    color: var(--brand);
    font-weight: 600;
  }
  .company__dot {
    flex: none;
    border-radius: 50%;
    background: var(--brand);
  }

  /* Front */
  .company--front {
    position: absolute;
    left: 60px;
    top: 0;
    bottom: 0;
    right: 50px;
    gap: 22px;
    font-size: 44px;
    line-height: 1.15;
  }
  .company--front .company__dot { width: 34px; height: 34px; }

  /* Back */
  .contact {
    position: absolute;
    left: 38px;
    top: 28px;
    list-style: none;
    color: var(--muted);
    font-size: 14px;
    font-weight: 500;
  }
  .contact__item { display: flex; align-items: center; gap: 10px; height: 24px; }
  .contact__icon { width: 13px; height: 13px; fill: var(--text); }

  .company--back {
    position: absolute;
    right: 30px;
    top: 30px;
    width: 170px;
    gap: 8px;
    font-size: 14px;
    line-height: 1.25;
  }
  .company--back .company__dot { width: 12px; height: 12px; }

  .person-name {
    position: absolute;
    left: 38px;
    top: 100px;
    color: var(--text);
    font-size: 40px;
    font-weight: 500;
    letter-spacing: 1px;
  }
  .divider {
    position: absolute;
    left: 38px;
    top: 160px;
    width: 484px;
    height: 3px;
    background: var(--rule);
  }
  .services {
    position: absolute;
    left: 38px;
    top: 180px;
    list-style: none;
    color: var(--text);
    font-size: 21px;
    font-weight: 500;
    line-height: 30px;
  }
</style>
</head>
<body>

  <section class="card card--front" aria-label="Business card front">
    <div class="company company--front">
      <span class="company__dot" aria-hidden="true"></span>
      <span class="company__name">FernGlen Plumbing Services</span>
    </div>
  </section>

  <section class="card card--back" aria-label="Business card back">
    <ul class="contact">
      <li class="contact__item">
        <svg class="contact__icon" viewBox="0 0 24 24" aria-hidden="true"><path d="M6.6 10.8a15.1 15.1 0 0 0 6.6 6.6l2.2-2.2a1 1 0 0 1 1-.25 11.4 11.4 0 0 0 3.6.57 1 1 0 0 1 1 1V20a1 1 0 0 1-1 1A17 17 0 0 1 3 4a1 1 0 0 1 1-1h3.5a1 1 0 0 1 1 1c0 1.25.2 2.45.57 3.57a1 1 0 0 1-.25 1z"/></svg>
        <span>123.456.7890</span>
      </li>
      <li class="contact__item">
        <svg class="contact__icon" viewBox="0 0 24 24" aria-hidden="true"><rect x="2" y="5" width="20" height="14" rx="1"/></svg>
        <span>sam@fernglenplumbing.com</span>
      </li>
    </ul>

    <div class="company company--back">
      <span class="company__dot" aria-hidden="true"></span>
      <span class="company__name">FernGlen Plumbing Services</span>
    </div>

    <h1 class="person-name">Sam Carter</h1>
    <div class="divider"></div>

    <ul class="services">
      <li>Domestic Plumbing</li>
      <li>Commercial Plumbing</li>
      <li>Roofing</li>
      <li>Gasfitting</li>
    </ul>
  </section>

</body>
</html>
```